5-6 page Website Design- Harbor Lantern Program, including 2 videos

We need an elegantly simple and beautiful website for the Harbor Lantern Program (HLP), a 6-month program for founders and leaders of startups who want to shift from Actors to Authors in their leadership.
At a minimum, the website will include:
Home Page
Program Description--Why Actor to Author?
Program Timeline and Structure
Testimonials and Past Clients (this page will include a testimonials video and text)
Team
FAQs
I'd like to see two versions of The Home Page/Landing Page:
1. Just an image with the words
If your startup is growing rapidly,
we can help you do the same.
HLP: The PLAYER to WRITER Shift
2. A place for a video describing the program
No payment integration on the website. Just information.
Startup founders and senior leaders

```html
<!DOCTYPE html>
<html lang="en">
<head>
<meta charset="utf-8">
<title>Harbor Lantern Program — Website Design</title>
<link href="https://fonts.googleapis.com/css2?family=Montserrat:wght@400;500;600;700&family=Roboto:wght@400&display=swap" rel="stylesheet">
<style>
:root{
  --stage:#2397d8;
  --brand:#0b57ad;
  --brand-light:#2196e0;
  --ink:#1f1f1f;
  --muted:#555;
  --soft:#f2f2f2;
  --white:#fff;
  --photo-a:#6d7b86;
  --photo-b:#3c4650;
}
*{box-sizing:border-box;margin:0;padding:0}
html,body{width:829px;height:1200px;overflow:hidden}
body{background:var(--stage);font-family:"Montserrat",sans-serif;color:var(--ink);position:relative}
.screen{position:absolute;background:var(--white);overflow:hidden;box-shadow:0 2px 6px rgba(0,0,0,.25)}
.abs{position:absolute}
.photo{position:absolute;background:linear-gradient(135deg,var(--photo-a),var(--photo-b))}
.brand{position:absolute;display:flex;align-items:center;gap:4px;font-weight:600;font-size:5.2px;line-height:1.05;letter-spacing:.2px;text-transform:uppercase}
.brand .dot{width:15px;height:15px;border-radius:50%;border:1.4px solid currentColor;flex:none}
.burger{position:absolute;width:11px;height:7px;border-top:1px solid #fff;border-bottom:1px solid #fff}
.burger::after{content:"";position:absolute;left:0;right:0;top:2px;border-top:1px solid #fff}
.btn{position:absolute;background:var(--brand-light);color:#fff;font-weight:600;font-size:5px;border-radius:9px;display:flex;align-items:center;justify-content:center;box-shadow:0 1px 2px rgba(0,0,0,.25);text-transform:uppercase}
.hero-line{position:absolute;left:0;right:0;text-align:center;color:#fff;font-weight:700;text-shadow:0 1px 2px rgba(0,0,0,.4)}
.section-title{position:absolute;left:0;right:0;text-align:center;font-weight:600;font-size:13.5px}
.rule{position:absolute;left:50%;width:36px;margin-left:-18px;height:1.4px;background:var(--brand-light)}
.copy{font-family:"Roboto",sans-serif;color:var(--muted)}
.footer{position:absolute;left:0;right:0;background:var(--brand);color:#fff;text-align:center}
.socials{display:flex;justify-content:center;gap:4px}
.socials span{width:13px;height:13px;border-radius:50%;background:#fff}
.contact{font-size:5.2px;display:flex;justify-content:center;gap:9px;align-items:center}
.contact b{font-size:7px;font-weight:700}
.legal{font-size:4.8px}
.card{position:absolute;width:97px;height:84px;background:#fff;box-shadow:0 1px 3px rgba(0,0,0,.15);border-radius:2px;overflow:hidden}
.card h4{background:var(--brand);color:#fff;height:23px;display:flex;align-items:center;justify-content:center;font-size:8px;font-weight:700}
.card ul{list-style:none;padding:8px 5px 0 5px}
.card li{font-size:4.2px;line-height:9px;padding-left:7px;position:relative}
.card li::before{content:"→";position:absolute;left:0;color:var(--brand-light)}
.member{position:absolute;width:100px;text-align:center}
.member .avatar{width:88px;height:88px;border-radius:50%;margin:0 auto;background:linear-gradient(135deg,#9aa3ab,#4e5862);box-shadow:0 0 0 2px #fff,0 1px 3px rgba(0,0,0,.2)}
.member h5{font-size:5.3px;font-weight:500;margin-top:5px}
.member p{font-size:3.9px;line-height:7.5px;margin-top:2px}
.nav{position:absolute;top:0;left:0;right:0;height:27px;background:#fff;display:flex;align-items:center}
.nav ul{list-style:none;display:flex;gap:10px;position:absolute;right:36px;font-size:4.2px}
.nav li.active{color:var(--brand-light)}
</style>
</head>
<body>

<!-- Landing version 1: image with statement -->
<section class="screen" style="left:15px;top:21px;width:386px;height:221px;background:var(--brand)">
  <div class="photo" role="img" aria-label="Team of startup founders talking in a bright office" style="inset:0;background:linear-gradient(120deg,#b9c4cc,#5f6f7c 60%,#3c4a56)"></div>
  <svg class="abs" style="left:0;top:0" width="386" height="221" viewBox="0 0 386 221">
    <path d="M0 155 C60 120 150 110 200 160 C240 195 310 175 386 145 L386 221 L0 221 Z" fill="#0b57ad"/>
    <circle cx="62" cy="146" r="10" fill="#2f78cc" opacity=".7"/>
    <circle cx="71" cy="153" r="9" fill="#2f78cc" opacity=".7"/>
    <circle cx="363" cy="171" r="10" fill="#2f78cc" opacity=".7"/>
    <circle cx="372" cy="178" r="9" fill="#2f78cc" opacity=".7"/>
  </svg>
  <div class="brand" style="left:159px;top:10px;color:#fff">
    <span class="dot"></span><span>Harbor<br>Lantern<br>Program</span>
  </div>
  <div class="burger" style="left:354px;top:15px"></div>
  <div class="abs" style="left:17px;top:174px;color:#fff;font-weight:700;font-size:9.4px;line-height:13.8px">
    If your startup is growing rapidly,<br>we can help you do the same.<br>HLP: The PLAYER to WRITER Shift
  </div>
  <div class="abs" style="left:270px;top:190px;color:#fff;font-size:5.3px;line-height:14px">
    <div>☏ Call Now - <b style="font-size:6.8px">+1 555 014 2290</b></div>
    <div>✉ info@HarborLanternProgram.com</div>
  </div>
</section>

<!-- Landing version 2: video -->
<section class="screen" style="left:15px;top:261px;width:386px;height:479px">
  <div class="photo" role="img" aria-label="Smiling group of young founders standing in a loft office, program video" style="left:0;top:0;width:386px;height:205px;background:linear-gradient(120deg,#8a6e52,#4c4038 55%,#6e7a86)"></div>
  <svg class="abs" style="left:0;top:186px" width="386" height="24" viewBox="0 0 386 24">
    <path d="M0 18 L386 0 L386 24 L0 24 Z" fill="#2196e0"/>
    <path d="M0 22 L386 4 L386 24 L0 24 Z" fill="#fff"/>
  </svg>
  <div class="brand" style="left:159px;top:9px;color:#fff">
    <span class="dot"></span><span>Harbor<br>Lantern<br>Program</span>
  </div>
  <div class="burger" style="left:354px;top:15px"></div>
  <svg class="abs" style="left:181px;top:74px" width="24" height="24" viewBox="0 0 24 24">
    <circle cx="12" cy="12" r="11.5" fill="none" stroke="#2196e0" stroke-opacity=".5"/>
    <circle cx="12" cy="12" r="9" fill="#2196e0"/>
    <path d="M10 8 L16 12 L10 16 Z" fill="#fff"/>
  </svg>
  <div class="hero-line" style="top:111px;font-size:9.4px;line-height:15.5px">If your startup is growing rapidly,&nbsp; we can help you do<br>the same.HLP: The PLAYER to WRITER Shift</div>

  <h2 class="abs" style="left:35px;top:245px;color:var(--brand);font-size:13.5px;font-weight:700">Program Description</h2>
  <p class="abs copy" style="left:36px;top:270px;width:156px;font-size:4.3px;line-height:9.4px">Well thanks Priya, sounds pretty simple...but what about when I've got 11 back-to-back meetings, a board meeting to prepare for with investors who have sky-high expectations, 6 new hires to onboard and 16 more to find, and–not least–a product to improve for the customers we are trying to serve and retain–only to wake up, rinse (maybe) and repeat tomorrow?? (We didn't even mention the team chat and email messages mounting in the background.) How could I possibly exit</p>
  <div class="btn" style="left:36px;top:341px;width:70px;height:16px">Get Started</div>
  <div class="photo" role="img" aria-label="Portrait of a smiling founder in glasses and a plaid shirt" style="left:206px;top:232px;width:142px;height:142px;border-radius:50%;box-shadow:0 0 0 2px #fff,0 1px 4px rgba(0,0,0,.2);background:linear-gradient(135deg,#b8c0c6,#6d5048)"></div>

  <footer class="footer" style="top:399px;height:80px;padding-top:16px">
    <div class="socials" aria-label="Social links"><span></span><span></span><span></span><span></span></div>
    <div class="contact" style="margin-top:9px"><span>☏ Call Now - <b>+1 555 014 2290</b></span><span>✉ info@HarborLanternProgram.com</span></div>
    <div class="legal" style="margin-top:10px">© 2022 All Rights Reserved</div>
  </footer>
</section>

<!-- Full desktop page -->
<section class="screen" style="left:419px;top:19px;width:386px;height:1149px">
  <div class="photo" role="img" aria-label="Workshop group seated in a bright white studio listening to a facilitator" style="left:0;top:27px;width:386px;height:222px;background:linear-gradient(120deg,#6b6e70,#3f4447 55%,#55595c)"></div>
  <svg class="abs" style="left:0;top:195px" width="386" height="55" viewBox="0 0 386 55">
    <path d="M0 22 Q193 74 386 22 L386 55 L0 55 Z" fill="#fff"/>
  </svg>
  <nav class="nav">
    <div class="brand" style="left:36px;top:6px;color:var(--brand)"><span class="dot"></span><span>Harbor<br>Lantern<br>Program</span></div>
    <ul>
      <li class="active">Home</li><li>Program</li><li>Program Timeline and Structure ⌄</li><li>Testimonials</li><li>Team</li><li>FAQs</li>
    </ul>
  </nav>
  <div class="hero-line" style="top:102px;font-size:9px;line-height:14px">If your startup is growing rapidly,&nbsp; we can help<br>you do the same.HLP: The PLAYER to WRITER Shift</div>
  <div class="btn" style="left:155px;top:136px;width:76px;height:16px">Get Started</div>
  <svg class="abs" style="left:182px;top:211px" width="24" height="6" viewBox="0 0 24 6">
    <circle cx="3" cy="3" r="2" fill="none" stroke="#fff" stroke-width=".8"/>
    <circle cx="9" cy="3" r="2" fill="none" stroke="#fff" stroke-width=".8"/>
    <circle cx="15" cy="3" r="2.2" fill="#fff"/>
    <circle cx="21" cy="3" r="2" fill="none" stroke="#fff" stroke-width=".8"/>
  </svg>

  <!-- Program description -->
  <h2 class="section-title" style="top:255px">Program Description</h2>
  <div class="rule" style="top:278px"></div>
  <p class="abs copy" style="left:36px;right:36px;top:288px;text-align:center;font-size:4.2px;line-height:9.1px">Well thanks Priya, sounds pretty simple...but what about when I've got 11 back-to-back meetings, a board meeting to prepare for with investors who have sky-high expectations, 6 new hires to onboard and 16 more to find, and–not least–a product to improve for the customers we are trying to serve and retain–only to wake up, rinse (maybe) and repeat tomorrow?? (We didn't even mention the team chat and email messages mounting in the background.) How could I possibly exit "busy anxiousness" and practice calm centeredness amidst this chaos? (Notice what you feel just reading that–does your body tighten a bit?)<br>Calm sounds nice–for vacation! I want results.</p>
  <div class="btn" style="left:155px;top:342px;width:76px;height:16px">Read More</div>

  <!-- Timeline -->
  <div class="abs" style="left:0;top:382px;width:386px;height:281px;background:var(--soft)"></div>
  <h2 class="section-title" style="top:408px;font-size:11px;text-transform:uppercase">Program Timeline and Structure</h2>
  <div class="rule" style="top:428px"></div>
  <div class="card" style="left:41px;top:441px"><h4>MONTH 1</h4><ul><li>Week 1: Kickoff Orientation Workshop</li><li>Week 2: 1on1 Exec Coaching Session</li><li>Week 3: Workshop</li></ul></div>
  <div class="card" style="left:144px;top:441px"><h4>MONTH 2</h4><ul><li>Week 1: 1st Retreat ("Leading Yourself")</li><li>Week 2: 1on1 Exec Coaching Session</li><li>Week 4: Workshop</li></ul></div>
  <div class="card" style="left:247px;top:441px"><h4>MONTH 3</h4><ul><li>Week 2: 1on1 Exec Coaching Session</li><li>Week 4: Workshop</li></ul></div>
  <div class="card" style="left:41px;top:531px"><h4>MONTH 4</h4><ul><li>Week 2: 1on1 Exec Coaching Session</li></ul></div>
  <div class="card" style="left:144px;top:531px"><h4>MONTH 5</h4><ul><li>Week 1: 2nd Retreat ("Leading Others, Leading Relationships")</li><li>Week 2: 1on1 Exec Coaching Session</li><li>Week 4: Workshop</li></ul></div>
  <div class="card" style="left:247px;top:531px"><h4>MONTH 6</h4><ul><li>Week 2: 1on1 Exec Coaching Session</li><li>Week 4: Concluding Workshop</li><li>Week 5: Concluding 1on1 Exec Coaching Session</li></ul></div>

  <!-- Testimonials -->
  <h2 class="section-title" style="top:673px">Testimonials and Past Clients</h2>
  <div class="rule" style="top:696px"></div>
  <div class="photo" role="img" aria-label="Testimonial video of a past client, a woman in glasses" style="left:36px;top:712px;width:142px;height:133px;background:linear-gradient(135deg,#c9b8a4,#7a6a60 60%,#5a79b8)"></div>
  <svg class="abs" style="left:98px;top:771px" width="14" height="14" viewBox="0 0 14 14"><circle cx="7" cy="7" r="6.5" fill="#fff"/><path d="M5.5 4.5 L10 7 L5.5 9.5 Z" fill="#777"/></svg>
  <div class="abs" style="left:194px;top:723px;color:var(--brand-light);font-size:26px;font-weight:700;line-height:1">“</div>
  <p class="abs copy" style="left:194px;top:745px;width:158px;font-style:italic;font-size:4.3px;line-height:9.1px">Lorem ipsum dolor sit amet, consectetur adipiscing elit, sed do eiusmod tempor incididunt ut labore et dolore magna aliqua. Ut enim ad minim veniam, quis nostrud exercitation ullamco laboris nisi ut aliquip ex ea commodo consequat. Duis aute irure dolor in reprehenderit in voluptate velit esse</p>
  <div class="abs" style="left:194px;top:796px;font-size:5.2px;font-weight:500">Tessa Marlowe</div>
  <div class="abs copy" style="left:194px;top:804px;font-size:4.2px">Lorem ipsum dolor</div>
  <div class="btn" style="left:194px;top:816px;width:105px;height:16px">View More Video Testimonials</div>

  <!-- Team -->
  <div class="abs" style="left:0;top:873px;width:386px;height:197px;background:var(--soft)"></div>
  <h2 class="section-title" style="top:895px">Team</h2>
  <div class="rule" style="top:918px"></div>
  <div class="abs" style="left:24px;top:964px;font-size:9px">‹</div>
  <div class="abs" style="left:356px;top:964px;font-size:9px">›</div>
  <div class="member" style="left:32px;top:928px"><div class="avatar" role="img" aria-label="Portrait of team member seated in a black t-shirt"></div><h5>Rowan Ellery</h5><p class="copy">Lorem ipsum dolor sit amet, consectetur adipiscing elit, sed do eiusmod tempor incididunt ut labore et dolore magna aliqua. Ut enim ad</p></div>
  <div class="member" style="left:143px;top:928px"><div class="avatar" role="img" aria-label="Portrait of team member with curly hair in green" style="background:linear-gradient(135deg,#e9c37a,#2fa05a)"></div><h5>Rowan Ellery</h5><p class="copy">Lorem ipsum dolor sit amet, consectetur adipiscing elit, sed do eiusmod tempor incididunt ut labore et dolore magna aliqua. Ut enim ad</p></div>
  <div class="member" style="left:253px;top:928px"><div class="avatar" role="img" aria-label="Portrait of senior team member in glasses" style="background:linear-gradient(135deg,#aab4be,#5b6f86)"></div><h5>Rowan Ellery</h5><p class="copy">Lorem ipsum dolor sit amet, consectetur adipiscing elit, sed do eiusmod tempor incididunt ut labore et dolore magna aliqua. Ut enim ad</p></div>

  <footer class="footer" style="top:1070px;height:79px;padding-top:15px">
    <div class="socials" aria-label="Social links"><span></span><span></span><span></span><span></span></div>
    <div class="contact" style="margin-top:9px"><span>☏ Call Now - <b>+1 555 014 2290</b></span><span>✉ info@HarborLanternProgram.com</span></div>
    <div class="legal" style="margin-top:10px">© 2022 All Rights Reserved</div>
  </footer>
</section>

</body>
</html>
```